Design concept Visual UI of future mobile app - healthcare

Hi,
I'm looking for a top designer, innovative with strong experience in user interface

The app will be connected to a future health website related to depression and addiction by helping the user to track the moods, tired, anxiety using this mobile app.

I attached the deck of the overall project but I can send you a specific presentation for the app only

thanks

Target Market(s)

Switzerland, UK, Germany and France

Industry/Entity Type

Mental Health

Logo Text

Health, hope

Font styles to use
Sans Serif

Colors
cee9f5
33a6d7
0692cd
0255a3
3276b5
85abd2

Requirements
Must have
• keep it simple, easy to navigate
• The user should be able to track the moods on a daily basis,
• sleep time, and rate how the feel on the day
• To be able to get information from the sync deck of vexlo
Nice to have
• to be able share this app with a friend

```html
<!DOCTYPE html>
<html lang="en">
<head>
<meta charset="utf-8">
<title>Sync Deck – App Screens</title>
<link href="https://fonts.googleapis.com/css2?family=Roboto:ital,wght@0,400;0,500;0,700;1,400&display=swap" rel="stylesheet">
<style>
:root{
  --page:#f2f2f2;
  --sky:#c4e4f3;
  --title:#33a6d7;
  --navy:#0255a3;
  --mid:#3276b5;
  --accent:#0692cd;
  --soft:#85abd2;
  --body-top:#e6e6e6;
  --body-bottom:#d6d6d6;
  --ink:#444;
  --text-grey:#555;
  --row-text:#777;
  --placeholder:#999;
  --bar:#111;
  --white:#fff;
  --line:#c9c9c9;
}
*{box-sizing:border-box;margin:0;padding:0}
html,body{width:1200px;height:800px;overflow:hidden}
body{background:var(--page);font-family:'Roboto',sans-serif;position:relative;color:var(--ink)}

.screen{position:absolute;top:228px;width:188px;height:334px;overflow:hidden;
  background:linear-gradient(var(--body-top),var(--body-bottom));box-shadow:0 0 0 1px #222}
.screen--messages{left:233px}
.screen--profile{left:510px}
.screen--settings{left:786px}

.status-bar{position:absolute;left:0;top:0;width:100%;height:12px;background:var(--bar);color:var(--white);
  font-size:5.5px;font-weight:400;display:flex;align-items:center;justify-content:space-between;padding:0 4px}
.status-bar .left,.status-bar .right{display:flex;align-items:center;gap:3px}
.status-bar .time{position:absolute;left:50%;transform:translateX(-50%)}

.app-header{position:absolute;left:0;top:12px;width:100%;height:31px;background:var(--sky);
  display:flex;align-items:center;justify-content:center}
.app-header h1{font-size:9px;font-weight:700;color:var(--title);letter-spacing:.3px}
.app-header .menu{position:absolute;left:20px;top:10px}
.app-header .prev{position:absolute;left:42px;top:9px}
.app-header .next{position:absolute;right:20px;top:9px}

.el{position:absolute}

.avatar{width:42px;height:50px;border-radius:3px}
.avatar--her{background:linear-gradient(135deg,#e9dcc0,#c9a77a 55%,#8b9a8c)}
.avatar--him{background:linear-gradient(135deg,#d8b38a,#a67c55 55%,#e7e2dc)}

.bubble{background:var(--white);border-radius:4px;padding:5px 5px 4px;box-shadow:0 1px 2px rgba(0,0,0,.25);
  font-size:3.9px;line-height:1.45;font-weight:500;color:var(--text-grey);white-space:normal}
.bubble::before{content:"";position:absolute;top:10px;width:0;height:0;border:4px solid transparent}
.bubble--in::before{left:-7px;border-right:4px solid var(--white);border-left:0}
.bubble--out::before{right:-7px;border-left:4px solid var(--white);border-right:0}
.bubble .meta{display:flex;justify-content:space-between;align-items:baseline;margin-bottom:5px}
.bubble .ago{color:var(--accent);font-size:3.6px;font-weight:400}
.bubble .who{color:var(--navy);font-weight:700;font-size:4.8px}
.bubble .attach{display:flex;justify-content:space-between;border-top:1px solid var(--soft);margin-top:3px;padding-top:2px;font-weight:400}
.bubble .attach b{color:var(--navy);font-weight:700}

.label{font-size:6px;font-weight:700;color:var(--mid)}
.field{background:var(--white);border:1px solid var(--line);box-shadow:inset 0 1px 1px rgba(0,0,0,.12);
  font-size:6px;color:var(--ink);padding:0 6px;display:flex;align-items:center}
.unit{font-size:5.5px;color:var(--soft)}
.radio{display:flex;align-items:center;gap:3px;font-size:5.5px;color:var(--soft)}
.radio i{width:6px;height:6px;border:1px solid #999;border-radius:50%;background:var(--white);position:relative}
.radio i.on::after{content:"";position:absolute;left:1px;top:1px;width:2px;height:2px;border-radius:50%;background:#333}

.group{background:linear-gradient(#eaeaea,#dedede);box-shadow:0 1px 2px rgba(0,0,0,.25)}
.row{height:22px;display:flex;align-items:center;justify-content:space-between;padding:0 6px;
  font-size:6px;font-weight:500;color:var(--row-text);border-bottom:1px solid #cfcfcf}
.row:last-child{border-bottom:0}
.row.input{font-style:italic;font-weight:400;color:var(--placeholder)}

.invite{background:linear-gradient(#3b8fd6,var(--navy));color:var(--white);border-radius:3px;
  font-size:6.3px;font-weight:400;display:flex;align-items:center;justify-content:center;box-shadow:0 0 0 1px #123}
</style>
</head>
<body>

<svg width="0" height="0" style="position:absolute" aria-hidden="true">
  <defs>
    <symbol id="menu" viewBox="0 0 12 10"><rect y="0" width="12" height="2" fill="#3276b5"/><rect y="4" width="12" height="2" fill="#3276b5"/><rect y="8" width="12" height="2" fill="#3276b5"/></symbol>
    <symbol id="chev-l" viewBox="0 0 6 10"><path d="M5 1L1 5l4 4" fill="none" stroke="#fff" stroke-width="1.3"/></symbol>
    <symbol id="chev-r" viewBox="0 0 6 10"><path d="M1 1l4 4-4 4" fill="none" stroke="#fff" stroke-width="1.3"/></symbol>
    <symbol id="chev-blue" viewBox="0 0 6 10"><path d="M1 1l4 4-4 4" fill="none" stroke="#0692cd" stroke-width="1.6"/></symbol>
    <symbol id="battery" viewBox="0 0 14 7"><rect x=".5" y=".5" width="12" height="6" rx="1" fill="none" stroke="#fff"/><rect x="1.5" y="1.5" width="10" height="4" fill="#fff"/><rect x="13" y="2.2" width="1" height="2.6" fill="#fff"/></symbol>
    <symbol id="wifi" viewBox="0 0 10 8"><path d="M1 3a6 6 0 0 1 8 0M2.6 4.6a3.6 3.6 0 0 1 4.8 0" fill="none" stroke="#fff" stroke-width="1"/><circle cx="5" cy="6.6" r=".9" fill="#fff"/></symbol>
    <symbol id="bt" viewBox="0 0 6 10"><path d="M1 3l4 4-2 2V1l2 2-4 4" fill="none" stroke="#fff" stroke-width=".8"/></symbol>
  </defs>
</svg>

<!-- Messages -->
<section class="screen screen--messages">
  <div class="status-bar">
    <span class="left">●●●○○ NOVA <svg width="7" height="6"><use href="#wifi"/></svg></span>
    <span class="time">4:21 PM</span>
    <span class="right"><svg width="4" height="6"><use href="#bt"/></svg>100% <svg width="12" height="6"><use href="#battery"/></svg></span>
  </div>
  <header class="app-header">
    <svg class="menu" width="12" height="10"><use href="#menu"/></svg>
    <svg class="prev" width="6" height="10"><use href="#chev-l"/></svg>
    <h1>MESSAGES</h1>
    <svg class="next" width="6" height="10"><use href="#chev-r"/></svg>
  </header>

  <div class="el avatar avatar--her" style="left:12px;top:48px" role="img" aria-label="Portrait photo of Lena Marsh"></div>
  <div class="el bubble bubble--in" style="left:68px;top:50px;width:97px;height:38px">
    <div class="meta"><span class="ago">7 minutes ago</span><span class="who">Lena Marsh</span></div>
    If you want to improve your mood try gentle exercises or go for a walk for 30 minutes
  </div>

  <div class="el bubble bubble--out" style="left:28px;top:110px;width:97px;height:38px">
    <div class="meta"><span class="ago">5 minutes ago</span><span class="who">Tobias Reed</span></div>
    Thanks. Do you have any instruction files?
  </div>
  <div class="el avatar avatar--him" style="left:137px;top:110px" role="img" aria-label="Portrait photo of Tobias Reed"></div>

  <div class="el avatar avatar--her" style="left:12px;top:172px" role="img" aria-label="Portrait photo of Lena Marsh"></div>
  <div class="el bubble bubble--in" style="left:68px;top:173px;width:110px;height:43px">
    <div class="meta"><span class="ago">3 minutes ago</span><span class="who">Lena Marsh</span></div>
    Here
    <div class="attach"><b>Attachment</b><span>instruction.jpg</span></div>
  </div>

  <div class="el bubble bubble--out" style="left:25px;top:236px;width:97px;height:38px">
    <div class="meta"><span class="ago">1 minute ago</span><span class="who">Tobias Reed</span></div>
    Thanks.
  </div>
  <div class="el avatar avatar--him" style="left:134px;top:236px" role="img" aria-label="Portrait photo of Tobias Reed"></div>

  <div class="el bubble bubble--out" style="left:28px;top:302px;width:97px;height:38px">
    <div class="meta"><span class="ago">1 minute ago</span><span class="who">Tobias Reed</span></div>
    Thanks.
  </div>
  <div class="el avatar avatar--him" style="left:137px;top:302px" role="img" aria-label="Portrait photo of Tobias Reed"></div>
</section>

<!-- Profile -->
<section class="screen screen--profile">
  <div class="status-bar">
    <span class="left">●●●○○ NOVA <svg width="7" height="6"><use href="#wifi"/></svg></span>
    <span class="time">4:21 PM</span>
    <span class="right"><svg width="4" height="6"><use href="#bt"/></svg>100% <svg width="12" height="6"><use href="#battery"/></svg></span>
  </div>
  <header class="app-header">
    <svg class="menu" width="12" height="10"><use href="#menu"/></svg>
    <svg class="prev" width="6" height="10"><use href="#chev-l"/></svg>
    <h1>PROFILE</h1>
    <svg class="next" width="6" height="10"><use href="#chev-r"/></svg>
  </header>

  <span class="el label" style="left:34px;top:62px">Name</span>
  <div class="el field" style="left:34px;top:71px;width:108px;height:17px">Tobias Hale</div>

  <span class="el label" style="left:34px;top:93px">Gender</span>
  <span class="el radio" style="left:65px;top:108px"><i class="on"></i>Male</span>
  <span class="el radio" style="left:102px;top:108px"><i></i>Female</span>

  <span class="el label" style="left:34px;top:118px">Age</span>
  <div class="el field" style="left:34px;top:127px;width:36px;height:16px">22</div>

  <span class="el label" style="left:34px;top:149px">Height</span>
  <div class="el field" style="left:34px;top:159px;width:18px;height:16px"></div>
  <span class="el unit" style="left:58px;top:164px">ft</span>
  <div class="el field" style="left:70px;top:159px;width:18px;height:16px"></div>
  <span class="el unit" style="left:91px;top:164px">in</span>

  <span class="el label" style="left:34px;top:180px">Weight</span>
  <div class="el field" style="left:34px;top:189px;width:18px;height:15px"></div>
  <span class="el unit" style="left:58px;top:193px">lbs</span>

  <span class="el label" style="left:34px;top:210px">Medications</span>
  <div class="el field" style="left:34px;top:222px;width:108px;height:27px"></div>

  <span class="el label" style="left:34px;top:257px">Consultations</span>
  <div class="el field" style="left:34px;top:268px;width:108px;height:28px"></div>
</section>

<!-- Settings -->
<section class="screen screen--settings">
  <div class="status-bar">
    <span class="left">●●●○○ NOVA <svg width="7" height="6"><use href="#wifi"/></svg></span>
    <span class="time">4:21 PM</span>
    <span class="right"><svg width="4" height="6"><use href="#bt"/></svg>100% <svg width="12" height="6"><use href="#battery"/></svg></span>
  </div>
  <header class="app-header">
    <svg class="menu" width="12" height="10"><use href="#menu"/></svg>
    <svg class="prev" width="6" height="10"><use href="#chev-l"/></svg>
    <h1>SETTING</h1>
    <svg class="next" width="6" height="10"><use href="#chev-r"/></svg>
  </header>

  <div class="el group" style="left:32px;top:51px;width:125px">
    <div class="row">Version 1.0.1 <svg width="5" height="7"><use href="#chev-blue"/></svg></div>
    <div class="row">More info <svg width="5" height="7"><use href="#chev-blue"/></svg></div>
  </div>

  <div class="el group" style="left:32px;top:109px;width:125px">
    <div class="row">Follow us on Linkora <svg width="5" height="7"><use href="#chev-blue"/></svg></div>
    <div class="row">Follow us on Chirpline <svg width="5" height="7"><use href="#chev-blue"/></svg></div>
    <div class="row">Sync Deck - App <svg width="5" height="7"><use href="#chev-blue"/></svg></div>
  </div>

  <div class="el group" style="left:32px;top:189px;width:125px">
    <div class="row input">Your name</div>
    <div class="row input">Friend name</div>
    <div class="row input">Your friend email</div>
  </div>

  <div class="el invite" style="left:50px;top:283px;width:97px;height:16px">Invite your friend</div>
</section>

</body>
</html>
```